Tellmora Corporate Stationery

Look for design of all new corporate stationery for an existing insurance broking business that is going through a redesign and move from older partners to younger family members. New Logo is attached. Company is Brisbane based.
Colours in the Logo is Hex #43bed8 and website features a lot of hex #17b8d8. Website front page "A plan to protect you" - headline. "Professional and Individual advice to protect your greatest assets" - tagline.

Stationery required: Business Cards, Letter head, Thank-you cards, Birthday cards, Presentation folders, With Compliment slips and a powerpoint template. We also would like to send a card to all customers with the something along of the lines of "something new".

Target Market(s)

Customers of Insurance business looking at superannuation, life and income protection insurance, investment advice and wills

Industry/Entity Type

Insurance Broker

Font styles to use
Other font styles liked:
• same as logo

Requirements
Must have
• The above designs for new stationery for the new business including:
• Business Cards, Letter head, Thank-you cards, Birthday cards, Presentation folders, With Compliment slips and a powerpoint template. We also would like to send a card to all customers with the something along of the lines of "something new".
Nice to have
• It is a new look - long time family business being passed to next generation - big focus on advice for YOU, individual advice etc..

```html
<!DOCTYPE html>
<html lang="en">
<head>
<meta charset="utf-8">
<title>Tellmora Business Card</title>
<link rel="stylesheet" href="https://fonts.googleapis.com/css2?family=Open+Sans:wght@400;600&display=swap">
<style>
  :root {
    --page-bg: #d9d6d2;
    --card-bg: #eef0f0;
    --card-edge: #ffffff;
    --ink: #2f3133;
    --accent: #2c9db6;
    --mark-grey: #55585b;
  }
  * { margin: 0; padding: 0; box-sizing: border-box; }
  html, body { width: 1200px; height: 969px; overflow: hidden; }
  body {
    background: var(--page-bg);
    font-family: "Open Sans", Arial, sans-serif;
    position: relative;
  }
  .business-card {
    position: absolute;
    left: 150px; top: 228px;
    width: 900px; height: 512px;
    background: var(--card-bg);
    border: 2px solid var(--card-edge);
    border-radius: 26px;
    box-shadow: 0 10px 30px rgba(0,0,0,0.15);
    overflow: hidden;
  }
  .brand-circle {
    position: absolute;
    left: 22px; top: 8px;
  }
  .contact-block {
    position: absolute;
    right: 34px; top: 30px;
    text-align: right;
    color: var(--ink);
  }
  .person-name {
    font-size: 29px; font-weight: 600;
    color: var(--accent);
    letter-spacing: 0.5px;
    line-height: 38px;
  }
  .person-title {
    font-size: 22px; line-height: 32px;
    margin-bottom: 16px;
  }
  .address { font-size: 22px; line-height: 31px; margin-bottom: 16px; }
  .contact-list { list-style: none; }
  .contact-list li {
    font-size: 22px; line-height: 34.5px;
    display: flex; align-items: center; justify-content: flex-end; gap: 10px;
  }
  .contact-list svg { width: 20px; height: 20px; fill: var(--accent); }
  .company-name {
    position: absolute;
    right: 34px; top: 398px;
    text-align: right;
    color: var(--accent);
    font-weight: 600;
    text-transform: uppercase;
  }
  .company-name .word { font-size: 46px; line-height: 52px; letter-spacing: 3px; display: block; }
  .company-name .descriptor { font-size: 27px; line-height: 32px; letter-spacing: 2px; display: block; }
</style>
</head>
<body>
  <div class="business-card">
    <svg class="brand-circle" width="500" height="500" viewBox="0 0 500 500" aria-hidden="true">
      <circle cx="250" cy="250" r="235" fill="none" stroke="var(--mark-grey)" stroke-width="18" opacity="0.85"/>
    </svg>

    <div class="contact-block">
      <p class="person-name">DANIEL HARLOW</p>
      <p class="person-title">CEO/FOUNDER</p>
      <p class="address">4120 Wattle Crescent<br>Brisbane, Queensland 4000</p>
      <ul class="contact-list">
        <li>07 3184 2260
          <svg viewBox="0 0 24 24"><path d="M6.6 10.8a15 15 0 0 0 6.6 6.6l2.2-2.2c.3-.3.7-.4 1-.2 1.1.4 2.3.6 3.6.6.6 0 1 .4 1 1V20c0 .6-.4 1-1 1A17 17 0 0 1 3 4c0-.6.4-1 1-1h3.5c.6 0 1 .4 1 1 0 1.3.2 2.5.6 3.6.1.3 0 .7-.2 1z"/></svg>
        </li>
        <li>0412 557 318
          <svg viewBox="0 0 24 24"><path d="M7 1h10a2 2 0 0 1 2 2v18a2 2 0 0 1-2 2H7a2 2 0 0 1-2-2V3a2 2 0 0 1 2-2zm0 3v14h10V4zm5 15.5a1 1 0 1 0 0 2 1 1 0 0 0 0-2z"/></svg>
        </li>
        <li>07 3184 2261
          <svg viewBox="0 0 24 24"><path d="M6 2h12v5H6zM3 8h18a1 1 0 0 1 1 1v8h-4v5H6v-5H2V9a1 1 0 0 1 1-1zm5 8v4h8v-4z"/></svg>
        </li>
        <li>daniel@tellmora.com
          <svg viewBox="0 0 24 24"><path d="M2 5h20v14H2zm2 2v.5l8 5 8-5V7zm0 2.8V17h16V9.8l-8 5z"/></svg>
        </li>
        <li>www.tellmora.com
          <svg viewBox="0 0 24 24"><circle cx="12" cy="12" r="10"/><path d="M2 12h20M12 2c3 3 3 17 0 20M12 2c-3 3-3 17 0 20" stroke="#eef0f0" stroke-width="1.4" fill="none"/></svg>
        </li>
      </ul>
    </div>

    <p class="company-name">
      <span class="word">Tellmora</span>
      <span class="descriptor">Financial Group</span>
    </p>
  </div>
</body>
</html>
```